Business Card and Simple Logo Desgin

New Zealand based start up company "Vesta Advisory LTD" requires business cards and simple logo design.

Card Content.

Vesta Advisory LTD

Rebecca Thornbury
CA, BMS (Hons)

r.thornbury@vestaadvisory.co.nz
PH +64 21 574 613

Target Market(s)

Corporate Business in IT, Finance and accounting.

Industry/Entity Type

Business

```html
<!DOCTYPE html>
<html lang="en">
<head>
<meta charset="utf-8">
<title>Vesta Advisory LTD — Business Card</title>
<link rel="stylesheet" href="https://fonts.googleapis.com/css2?family=Source+Sans+3:wght@400;600&display=swap">
<style>
  :root {
    --page-bg: #1a1a1b;
    --card-top: #2b2f33;
    --card-mid: #1b1e21;
    --card-deep: #0f1113;
    --sheen: rgba(255, 255, 255, 0.06);
    --text-light: #e6e8ea;
    --text-soft: #c4c8cc;
    --brand: #d9dcdf;
    --mark: #b8bcc0;
  }

  * { margin: 0; padding: 0; box-sizing: border-box; }

  html, body {
    width: 1200px;
    height: 900px;
    overflow: hidden;
    background: var(--page-bg);
  }

  .canvas {
    width: 1200px;
    height: 900px;
    display: flex;
    align-items: center;
    justify-content: center;
  }

  .business-card {
    position: relative;
    width: 840px;
    height: 480px;
    border-radius: 18px;
    background:
      linear-gradient(115deg, transparent 38%, var(--sheen) 52%, transparent 66%),
      linear-gradient(160deg, var(--card-top) 0%, var(--card-mid) 55%, var(--card-deep) 100%);
    box-shadow: 0 24px 60px rgba(0, 0, 0, 0.55);
    font-family: "Source Sans 3", "Myriad Pro", sans-serif;
    color: var(--text-light);
    overflow: hidden;
  }

  .brand {
    position: absolute;
    left: 64px;
    top: 58px;
    display: flex;
    align-items: center;
    gap: 22px;
  }

  .brand-mark {
    width: 54px;
    height: 54px;
    border-radius: 50%;
    background: var(--mark);
  }

  .brand-name {
    font-size: 34px;
    font-weight: 600;
    color: var(--brand);
    letter-spacing: 0.2px;
  }

  .holder {
    position: absolute;
    left: 64px;
    top: 270px;
  }

  .holder-name {
    font-size: 38px;
    font-weight: 400;
    color: var(--text-light);
    line-height: 1.1;
  }

  .holder-credentials {
    margin-top: 6px;
    font-size: 24px;
    color: var(--text-soft);
  }

  .contact {
    position: absolute;
    left: 64px;
    bottom: 48px;
    font-size: 26px;
    line-height: 1.3;
    color: var(--text-soft);
    list-style: none;
  }
</style>
</head>
<body>
  <main class="canvas">
    <article class="business-card">
      <header class="brand">
        <span class="brand-mark" aria-hidden="true"></span>
        <span class="brand-name">Vesta Advisory LTD</span>
      </header>

      <section class="holder">
        <h1 class="holder-name">Rebecca Thornbury</h1>
        <p class="holder-credentials">CA, BMS (Hons)</p>
      </section>

      <ul class="contact">
        <li class="contact-phone">PH +64 21 574 613</li>
        <li class="contact-email">r.thornbury@vestaadvisory.co.nz</li>
      </ul>
    </article>
  </main>
</body>
</html>
```